Stylish new business card needed!

Hello everyone! I am in need of a new business card design for an alarm company here in Hurricane WV. I have all fonts, color codes and logos provided for you use! We are a young company and like the style of a clean sleek looking business card. Would like it double sided, one side holding the logo and the other with your design!
Target Market(s)
The people that are looking for the newest tech for home automation and security
Industry/Entity Type
Alarm services; Home automation
Contact Information for Business Card
Name of person; position (Sales; Installer); Phone Number (555.418.7260); Employee cell Number; Website (www.GuardedByVelk.example); Employee Email; Double sided
Look and feel
Each slider illustrates characteristics of the customer's brand and the style your logo design should communicate.

```html
<!DOCTYPE html>
<html lang="en">
<head>
<meta charset="utf-8">
<title>Guarded By Velk — Business Card</title>
<link rel="stylesheet" href="https://fonts.googleapis.com/css2?family=Arimo:wght@400;700&display=swap">
<style>
  :root {
    --backdrop: #2b2b2d;
    --card-white: #f5f5f5;
    --brand-orange: #ec8a4c;
    --brand-gray: #8e8e8e;
    --pattern-gray: #8a8a8a;
    --pattern-light: #a3a3a3;
    --ink: #111111;
  }
  * { box-sizing: border-box; margin: 0; padding: 0; }
  html, body { width: 1200px; height: 780px; overflow: hidden; }
  body {
    background: var(--backdrop);
    font-family: "Arimo", Arial, sans-serif;
    display: flex;
    align-items: center;
    justify-content: center;
    gap: 40px;
  }
  .card {
    position: relative;
    width: 540px;
    height: 309px;
    overflow: hidden;
    box-shadow: 0 10px 24px rgba(0,0,0,0.45);
  }
  /* Front */
  .card-front { background: var(--card-white); }
  .front-swoosh { position: absolute; inset: 0; }
  .holder-name {
    position: absolute; left: 96px; top: 34px;
    font-size: 27px; font-weight: 700; letter-spacing: 0.2px;
  }
  .holder-name .first { color: var(--brand-orange); }
  .holder-name .last { color: var(--brand-gray); }
  .holder-role {
    position: absolute; left: 142px; top: 70px;
    font-size: 15px; color: var(--ink);
  }
  .brand-block {
    position: absolute; left: 300px; top: 22px; width: 210px;
    text-align: center;
  }
  .brand-kicker {
    font-size: 14px; font-weight: 700; color: var(--brand-orange);
    letter-spacing: 1px; text-transform: uppercase;
  }
  .brand-name {
    font-size: 78px; font-weight: 400; color: var(--brand-gray);
    line-height: 0.95; letter-spacing: 2px;
  }
  .brand-tagline {
    font-size: 7.5px; font-weight: 700; color: var(--brand-orange);
    letter-spacing: 0.6px; text-transform: uppercase; margin-top: 4px;
  }
  .divider {
    position: absolute; left: 226px; top: 150px;
    width: 2px; height: 112px; background: var(--ink);
  }
  .contact-list {
    position: absolute; left: 244px; top: 158px;
    list-style: none;
  }
  .contact-list li {
    display: flex; align-items: center; gap: 9px;
    font-size: 15.5px; color: var(--ink); line-height: 24px;
  }
  .contact-list svg { width: 13px; height: 13px; flex: none; }
  /* Back */
  .card-back { background: var(--pattern-gray); }
  .back-pattern {
    position: absolute; inset: 0;
    background: linear-gradient(135deg, var(--pattern-light), var(--pattern-gray) 60%, #7c7c7c);
  }
  .back-mark {
    position: absolute; right: 70px; bottom: 78px;
    color: #ffffff; font-size: 30px; font-weight: 400; letter-spacing: 1px;
  }
</style>
</head>
<body>

  <section class="card card-front" aria-label="Card front">
    <svg class="front-swoosh" viewBox="0 0 540 309" preserveAspectRatio="none" aria-hidden="true">
      <path d="M0,58 C40,200 210,280 540,292 L540,309 L0,309 Z" fill="var(--brand-orange)"/>
      <path d="M0,58 C40,200 210,280 540,292 L540,290 C230,270 70,200 30,60 Z" fill="var(--card-white)"/>
      <path d="M44,44 C80,180 240,262 500,280" fill="none" stroke="var(--brand-gray)" stroke-width="4" stroke-linecap="round"/>
    </svg>

    <h1 class="holder-name"><span class="first">Mara</span> <span class="last">Kovel</span></h1>
    <p class="holder-role">Sales; Installer</p>

    <div class="brand-block">
      <p class="brand-kicker">Guarded By</p>
      <p class="brand-name">Velk</p>
      <p class="brand-tagline">Automation and Security Services</p>
    </div>

    <div class="divider"></div>

    <ul class="contact-list">
      <li>
        <svg viewBox="0 0 16 16" aria-hidden="true"><path d="M3 1 L6 1 L7 5 L5 6.5 C6 9 7 10 9.5 11 L11 9 L15 10 L15 13 C15 14 14 15 13 15 C6 15 1 10 1 3 C1 2 2 1 3 1 Z" fill="var(--brand-orange)"/></svg>
        555.418.7260
      </li>
      <li>
        <svg viewBox="0 0 16 16" aria-hidden="true"><rect x="4" y="1" width="8" height="14" rx="1.5" fill="none" stroke="var(--brand-orange)" stroke-width="1.6"/><circle cx="8" cy="12.5" r="0.9" fill="var(--brand-orange)"/></svg>
        555.902.3184
      </li>
      <li>
        <svg viewBox="0 0 16 16" aria-hidden="true"><circle cx="8" cy="8" r="6.5" fill="none" stroke="var(--brand-orange)" stroke-width="1.6"/><path d="M1.5 8 H14.5 M8 1.5 C5 5 5 11 8 14.5 M8 1.5 C11 5 11 11 8 14.5" fill="none" stroke="var(--brand-orange)" stroke-width="1.2"/></svg>
        www.GuardedByVelk.example
      </li>
      <li>
        <svg viewBox="0 0 16 16" aria-hidden="true"><rect x="1" y="3" width="14" height="10" rx="1" fill="var(--brand-orange)"/><path d="M1.5 3.5 L8 9 L14.5 3.5" fill="none" stroke="#ffffff" stroke-width="1.3"/></svg>
        info@GuardedByVelk.example
      </li>
    </ul>
  </section>

  <section class="card card-back" aria-label="Card back">
    <div class="back-pattern" role="img" aria-label="Repeating embossed brand-name pattern in grey tones"></div>
    <p class="back-mark">Velk</p>
  </section>

</body>
</html>
```